real esate business card with company logo and name

we need a business card design for a real esate company

The company name is Walsh & Brand Pty Ltd, and we have our logo designed and will upload. We want classic or moden feel. Black or white background. looks more textured. Should include folowinginformations
Owen Walsh and Lucy Brand
Sales Agents & Onsite Manager
p: 07 5948 2063
F: 07 5948 2174
M:0431 857 219
3/42 Marlow Crescent, FERNLEA QLD 4213

We want this business card looks professonal. Thank you in advance.

Industry/Entity Type

Real Estate Agent

Contact Information for Business Card

Owen Walsh and Lucy Brand
Onsite Manager & Sales Agents
p: 07 5948 2063
M:0431 857 219

Font styles to use
Serif

Colors
000000
fbfbfb
333333
959595

Requirements
Must have
• company logo and name, black or white back ground

```html
<!DOCTYPE html>
<html lang="en">
<head>
<meta charset="utf-8">
<title>Walsh &amp; Brand Pty Ltd — Business Card</title>
<link rel="stylesheet" href="https://fonts.googleapis.com/css2?family=Open+Sans:wght@400&family=Montserrat:wght@500&family=Playfair+Display:wght@400;700&display=swap">
<style>
  :root {
    --stage: #a5a5a5;
    --label: #333333;
    --card-dark: #4a4a4a;
    --card-edge: #333333;
    --card-glow: #8a8a8a;
    --band-light: #e8e8e8;
    --ink-light: #eeeeee;
    --ink-dark: #333333;
  }
  * { margin: 0; padding: 0; box-sizing: border-box; }
  html, body { width: 1200px; height: 1200px; overflow: hidden; }
  body { background: var(--stage); position: relative; font-family: "Playfair Display", serif; font-variant-numeric: lining-nums; }

  .side-label {
    position: absolute; left: 70px;
    font-family: "Open Sans", sans-serif; font-size: 48px; color: var(--label);
  }
  .side-label--front { top: 30px; }
  .side-label--back { top: 595px; left: 82px; }

  .card { position: absolute; left: 223px; width: 850px; height: 520px; overflow: hidden; }

  /* Front */
  .card--front {
    top: 41px;
    background: radial-gradient(ellipse 62% 70% at 50% 45%, var(--card-glow) 0%, #5a5a5a 55%, var(--card-edge) 100%);
  }
  .brand-mark {
    position: absolute; left: 0; right: 0; top: 165px;
    display: flex; align-items: center; justify-content: center; gap: 16px;
    font-size: 58px; font-weight: 400; color: var(--ink-light);
  }
  .brand-mark__square { width: 22px; height: 22px; background: var(--ink-light); }
  .company-line {
    position: absolute; left: 0; right: 0; top: 323px; text-align: center;
    font-family: "Montserrat", sans-serif; font-weight: 500; font-size: 17px;
    letter-spacing: 1px; color: var(--ink-light);
  }
  .tagline {
    position: absolute; left: 0; right: 0; top: 385px; text-align: center;
    font-size: 55px; font-weight: 700; letter-spacing: -1.5px; color: var(--ink-light);
  }

  /* Back */
  .card--back { top: 604px; background: var(--card-dark); }
  .bands { position: absolute; inset: 0; }
  .person { position: absolute; left: 106px; font-size: 40px; font-weight: 700; letter-spacing: -1px; line-height: 1; }
  .person--owen { top: 12px; color: var(--ink-dark); }
  .person--lucy { top: 70px; color: var(--ink-light); }
  .role { position: absolute; left: 406px; font-size: 32px; font-weight: 400; line-height: 1; }
  .role--sales { top: 14px; color: var(--ink-light); }
  .role--manager { top: 72px; color: var(--ink-dark); }

  .back-brand {
    position: absolute; left: 40px; width: 300px; top: 275px;
    display: flex; flex-direction: column; align-items: center; gap: 18px; color: var(--ink-light);
  }
  .back-brand__name { display: flex; align-items: center; gap: 10px; font-size: 34px; font-weight: 400; }
  .back-brand__square { width: 14px; height: 14px; background: var(--ink-light); }
  .back-brand__company { font-family: "Montserrat", sans-serif; font-weight: 500; font-size: 12px; letter-spacing: .6px; }

  .divider {
    position: absolute; left: 348px; top: 216px; width: 2px; height: 232px;
    background: linear-gradient(to bottom, rgba(238,238,238,0), var(--ink-light) 50%, rgba(238,238,238,0));
  }

  .contacts { position: absolute; left: 400px; top: 228px; list-style: none; color: var(--ink-light); font-size: 24px; }
  .contacts li { display: flex; align-items: center; height: 41.5px; }
  .contacts svg { width: 26px; height: 22px; margin-right: 6px; fill: var(--ink-light); flex: none; }
  .contacts .indent { padding-left: 32px; }
</style>
</head>
<body>
  <div class="side-label side-label--front">Front :</div>
  <section class="card card--front">
    <div class="brand-mark"><span class="brand-mark__square"></span>Walsh &amp; Brand</div>
    <div class="company-line">WALSH &amp; BRAND PTY LTD.</div>
    <h1 class="tagline">Real Estate Agent</h1>
  </section>

  <div class="side-label side-label--back">Back :</div>
  <section class="card card--back">
    <svg class="bands" width="850" height="520" viewBox="0 0 850 520">
      <polygon points="0,0 397,0 378,60 0,60" fill="var(--band-light)"/>
      <polygon points="373,60 850,60 850,118 353,118" fill="var(--band-light)"/>
    </svg>
    <div class="person person--owen">OWEN WALSH</div>
    <div class="role role--sales">sales agents</div>
    <div class="person person--lucy">LUCY BRAND</div>
    <div class="role role--manager">onsite manager</div>

    <div class="back-brand">
      <div class="back-brand__name"><span class="back-brand__square"></span>Walsh &amp; Brand</div>
      <div class="back-brand__company">WALSH &amp; BRAND PTY LTD.</div>
    </div>

    <div class="divider"></div>

    <ul class="contacts">
      <li><svg viewBox="0 0 26 22"><path d="M9 2c2 0 3 1 3 2l-1 3c0 1-2 1-2 2v4c0 1 2 1 2 2l1 3c0 1-1 2-3 2-2-1-3-4-3-9s1-8 3-9z"/></svg>: 0431 857 219</li>
      <li><svg viewBox="0 0 26 22"><rect x="7" y="1" width="12" height="6"/><rect x="2" y="7" width="22" height="9" rx="2"/><rect x="7" y="13" width="12" height="8" fill="var(--card-dark)" stroke="var(--ink-light)" stroke-width="2"/></svg>: 07 5948 2174</li>
      <li><svg viewBox="0 0 26 22"><path d="M2 8c0-4 22-4 22 0v2h-6V7H8v3H2z"/><path d="M7 11h12l4 9H3z"/><circle cx="13" cy="15.5" r="2.5" fill="var(--card-dark)"/></svg>: 07 5948 2063</li>
      <li><svg viewBox="0 0 26 22"><path d="M13 1 1 12h4v9h6v-6h4v6h6v-9h4z"/></svg>: 3/42 Marlow Crescent</li>
      <li class="indent">Fernlea QLD 4213</li>
    </ul>
  </section>
</body>
</html>
```